Kelvaro.ch is looking for business card letterhead and envelope C5 with WOW effect

We need a strong business card for our company Kelvaro.ch, logo is available. You want a black or dark background on which the logo Stark r% 26 # 252; appears. Letterhead and envelope in C5 format should be in a similar design, but does not have to be We need a strong business card for our company Kelvaro.ch, logo is available. A black or dark background is desired, on which the logo Stark comes across. The letterhead and the envelope in C5 format should have a similar design.

Target Market(s)

Private customers as well as entrepreneurs

Contact Information for Business Card

E-mail: info@kelvaro-example.ch
Web.www.Kelvaro-example.ch
Tel: +41 ( 0 ) 79 482 6037
Adresse:
Lindenweg 14
9406 Tarnbach

Hier kann man Icons verwenden für Email,Tel und Adressse

Font styles to use
Other font styles liked:
• Dubai,bold

Colors

Designer to choose colors to be used in the design.

Requirements
Must have
• WOW effect
Nice to have
• R% 26 # 252; back business card with our service listings. - VEHICLE LABELING - SHOP WINDOW LABELING - STICKERS AND MUCH MORE ... in red color

```html
<!DOCTYPE html>
<html lang="en">
<head>
<meta charset="utf-8">
<title>Kelvaro.ch – Business Card</title>
<link href="https://fonts.googleapis.com/css2?family=Lato:wght@400;700;900&display=swap" rel="stylesheet">
<style>
  :root {
    --backdrop: #dedede;
    --card-light: #ffffff;
    --card-dark: #070707;
    --accent: #fcc419;
    --ink: #111111;
    --muted: #8a8a8a;
    --rule: #9a9a9a;
    --paper-text: #ffffff;
  }
  * { margin: 0; padding: 0; box-sizing: border-box; }
  html, body {
    width: 1200px;
    height: 960px;
    overflow: hidden;
    background: var(--backdrop);
    font-family: "Lato", Arial, sans-serif;
  }
  .canvas { position: relative; width: 1200px; height: 960px; }

  .card {
    position: absolute;
    left: 281px;
    width: 655px;
    height: 374px;
    border-radius: 26px;
  }
  .card--front { top: 80px; background: var(--card-light); }
  .card--back { top: 506px; background: var(--card-dark); }

  .brand {
    position: absolute;
    display: flex;
    align-items: center;
    gap: 14px;
  }
  .brand__dot {
    width: 46px;
    height: 46px;
    border-radius: 50%;
    background: var(--accent);
  }
  .brand__name {
    font-weight: 900;
    font-size: 26px;
    letter-spacing: 0.5px;
  }
  .card--front .brand { left: 64px; top: 162px; }
  .card--front .brand__name { color: var(--ink); }
  .card--back .brand { left: 50%; top: 50%; transform: translate(-50%, -50%); gap: 18px; }
  .card--back .brand__dot { width: 60px; height: 60px; }
  .card--back .brand__name { color: var(--paper-text); font-size: 32px; }

  .divider {
    position: absolute;
    left: 328px;
    top: 89px;
    width: 1.5px;
    height: 193px;
    background: var(--rule);
  }

  .contact {
    position: absolute;
    left: 352px;
    top: 88px;
    color: var(--muted);
    font-size: 17px;
    line-height: 1.4;
  }
  .contact__name {
    color: var(--accent);
    font-weight: 700;
    font-size: 27px;
    line-height: 1.2;
  }
  .contact__role { margin-bottom: 9px; }
  .contact__address { margin-bottom: 10px; }
  .contact__line {
    display: flex;
    align-items: center;
    gap: 8px;
    height: 24px;
  }
  .contact__icon { width: 14px; height: 14px; flex: none; }
</style>
</head>
<body>
<main class="canvas">

  <section class="card card--front" aria-label="Business card front">
    <div class="brand">
      <span class="brand__dot"></span>
      <span class="brand__name">KELVARO.CH</span>
    </div>

    <div class="divider"></div>

    <div class="contact">
      <p class="contact__name">Lukas Brenner</p>
      <p class="contact__role">Managing Director</p>
      <p class="contact__address">Lindenweg 14<br>9406 Tarnbach</p>

      <p class="contact__line">
        <svg class="contact__icon" viewBox="0 0 14 14" aria-hidden="true">
          <path d="M3 12 C1 9 3 4 8 2 L10 1 L11 3 L8 5 C6 6 5 8 5 10 L6 12 Z" fill="var(--accent)"/>
        </svg>
        +41 ( 0 ) 79 482 6037
      </p>
      <p class="contact__line">
        <svg class="contact__icon" viewBox="0 0 14 14" aria-hidden="true">
          <rect x="1" y="3" width="12" height="8" fill="var(--accent)"/>
          <path d="M1 3 L7 8 L13 3" fill="none" stroke="#fff" stroke-width="1.2"/>
        </svg>
        info@kelvaro-example.ch
      </p>
      <p class="contact__line">
        <svg class="contact__icon" viewBox="0 0 14 14" aria-hidden="true">
          <g fill="none" stroke="var(--accent)" stroke-width="1.2">
            <circle cx="7" cy="7" r="6"/>
            <ellipse cx="7" cy="7" rx="2.6" ry="6"/>
            <path d="M1 7 H13 M2 4 H12 M2 10 H12"/>
          </g>
        </svg>
        www.kelvaro-example.ch
      </p>
    </div>
  </section>

  <section class="card card--back" aria-label="Business card back">
    <div class="brand">
      <span class="brand__dot"></span>
      <span class="brand__name">KELVARO.CH</span>
    </div>
  </section>

</main>
</body>
</html>
```